Im open to ideas.. I was thinking on my business cards aswell as my logo. a place for my name. email. phone number and abn..

ive attched a file with my business logo. which i dont love the colours.. i was think a dark background with charcoal letters so something along those colour schumes but im open to ideas..

BRM Constructions

```html
<!DOCTYPE html>
<html lang="en">
<head>
<meta charset="UTF-8">
<title>BRM Constructions – Business Card</title>
<link href="https://fonts.googleapis.com/css2?family=Open+Sans:wght@400;600;700&display=swap" rel="stylesheet">
<style>
  :root {
    --bg: #3a302b;
    --card: #1e1e1e;
    --card-back: #1a1a1a;
    --text-light: #d9d9d9;
    --text-muted: #b5b5b5;
    --brand-light: #c9c9c9;
    --brand-dark: #0c0c0c;
  }
  * { margin: 0; padding: 0; box-sizing: border-box; }
  html, body {
    width: 1200px; height: 844px; overflow: hidden;
    background: var(--bg);
    font-family: "Open Sans", sans-serif;
  }
  .stage {
    position: relative; width: 1200px; height: 844px;
  }
  .card {
    position: absolute; top: 272px;
    width: 520px; height: 300px;
    border-radius: 3px;
    box-shadow: 0 10px 30px rgba(0,0,0,0.45);
  }
  .card--front { left: 60px; background: var(--card); }
  .card--back { left: 620px; background: var(--card-back); }

  .brand {
    position: absolute; right: 40px; top: 50px;
    display: flex; align-items: center; gap: 10px;
    color: var(--brand-light);
    font-weight: 700; font-size: 24px; letter-spacing: 1px;
    text-transform: uppercase;
  }
  .brand__mark {
    width: 14px; height: 14px; background: var(--brand-light);
  }

  .contact {
    position: absolute; left: 40px; bottom: 36px;
    color: var(--text-light);
  }
  .contact__name { font-size: 18px; font-weight: 600; line-height: 1.1; }
  .contact__role { font-size: 12px; color: var(--text-muted); margin-bottom: 14px; }
  .contact__abn { font-size: 13px; font-weight: 700; margin-bottom: 12px; }
  .contact__list { list-style: none; font-size: 13px; }
  .contact__item { display: flex; align-items: center; gap: 10px; line-height: 20px; }
  .contact__icon { width: 11px; height: 11px; fill: var(--text-light); }

  .brand-back {
    position: absolute; inset: 0;
    display: flex; align-items: center; justify-content: center;
    color: var(--brand-dark);
    font-weight: 700; font-size: 36px; letter-spacing: 2px;
    text-transform: uppercase;
  }
</style>
</head>
<body>
<main class="stage">
  <section class="card card--front" aria-label="Card front">
    <div class="brand">
      <span class="brand__mark"></span>
      <span class="brand__name">BRM Constructions</span>
    </div>
    <div class="contact">
      <p class="contact__name">Daniel Harper</p>
      <p class="contact__role">Managing Director</p>
      <p class="contact__abn">ABN NO: 67890</p>
      <ul class="contact__list">
        <li class="contact__item">
          <svg class="contact__icon" viewBox="0 0 12 12" aria-hidden="true"><path d="M2.5 0.5l2 2.2-1 1.3c.7 1.6 1.9 2.8 3.5 3.5l1.3-1 2.2 2-1 2.5C4.7 10.8 1.2 7.3.2 1.5z"/></svg>
          <span>(044)-555-0192</span>
        </li>
        <li class="contact__item">
          <svg class="contact__icon" viewBox="0 0 12 12" aria-hidden="true"><path d="M0 2h12v8H0z M1 3l5 3.5L11 3v-.2H1z" fill-rule="evenodd"/></svg>
          <span>info@brmbuild.com</span>
        </li>
        <li class="contact__item">
          <svg class="contact__icon" viewBox="0 0 12 12" aria-hidden="true"><circle cx="6" cy="6" r="5.5"/></svg>
          <span>www.brmbuild.com</span>
        </li>
      </ul>
    </div>
  </section>

  <section class="card card--back" aria-label="Card back">
    <div class="brand-back">BRM Constructions</div>
  </section>
</main>
</body>
</html>
```